A start up Private Wine Label for export to Asia.

We are looking for the best graphic design for our very first wine label Corvessa Wines and would like the following requirements:

1. Black background - explore and play around the shade of black
2. Gold Shimmery Colour Font
3. Font should be a cursive classic posh that says Corvessa Wines
4. We would like the front graphic design to be simple and elegant and has a traditional classic feel to it.

Target Market(s)

Small scale to test the upper class market for export to Asia

Font styles to use
Script

Colors

Designer to choose colors to be used in the design.

Requirements
Must have
• Gold font for the label Corvessa Wines with shimmery touch to it.
• Elegant black background.
• Simple but elegant design.
• Attractive to the upper class market in Asia.
Nice to have
• Explore and play around with your imagination.

```html
<!DOCTYPE html>
<html lang="en">
<head>
<meta charset="UTF-8">
<title>Corvessa Wines – Label</title>
<link href="https://fonts.googleapis.com/css2?family=Great+Vibes&display=swap" rel="stylesheet">
<style>
  :root {
    --canvas: #ffffff;
    --label-black: #000000;
    --label-glow: #1b1b1b;
    --gold: #d6ae45;
    --gold-light: #f1d77a;
    --gold-deep: #a9782a;
  }
  html, body {
    margin: 0;
    padding: 0;
    width: 1200px;
    height: 1200px;
    overflow: hidden;
    background: var(--canvas);
  }
  .label {
    position: absolute;
    left: 236px;
    top: 222px;
    width: 728px;
    height: 716px;
    background: radial-gradient(ellipse at 52% 52%, var(--label-glow) 0%, #0a0a0a 45%, var(--label-black) 100%);
    overflow: hidden;
  }
  .label__rule {
    position: absolute;
    left: 0;
    width: 100%;
    height: 3px;
    background: linear-gradient(90deg, var(--gold-deep), var(--gold-light), var(--gold-deep));
  }
  .label__rule--top { top: 0; }
  .label__rule--bottom { bottom: 0; }
  .label__border-ornament {
    position: absolute;
    left: 0;
    width: 100%;
    height: 76px;
    opacity: 0.55;
  }
  .label__border-ornament--top {
    top: 4px;
    background: linear-gradient(180deg, var(--gold-deep) 0%, rgba(169,120,42,0.35) 70%, rgba(0,0,0,0) 100%);
  }
  .label__border-ornament--bottom {
    bottom: 4px;
    background: linear-gradient(0deg, var(--gold-deep) 0%, rgba(169,120,42,0.35) 70%, rgba(0,0,0,0) 100%);
  }
  .brand {
    position: absolute;
    left: 0;
    width: 100%;
    text-align: center;
    font-family: "Great Vibes", cursive;
    color: var(--gold);
    margin: 0;
    font-weight: 400;
  }
  .brand__name {
    top: 250px;
    font-size: 150px;
    line-height: 1;
    letter-spacing: 1px;
  }
  .brand__tagline {
    top: 440px;
    font-size: 78px;
    line-height: 1;
    padding-left: 10px;
  }
</style>
</head>
<body>
  <main class="label">
    <div class="label__rule label__rule--top"></div>
    <div class="label__border-ornament label__border-ornament--top" role="img" aria-label="Gold lace ornament border with petal and teardrop motifs"></div>

    <h1 class="brand brand__name">Corvessa</h1>
    <p class="brand brand__tagline">Wines</p>

    <div class="label__border-ornament label__border-ornament--bottom" role="img" aria-label="Gold lace ornament border with petal and teardrop motifs"></div>
    <div class="label__rule label__rule--bottom"></div>
  </main>
</body>
</html>
```